Home page design for Drone video business (the Business focusses on home videos for realtors)

Dear reader,

*I NEED DESIGNS OF ALL THE PAGES*
We need a first design of a homepage and of 4 other pages of the website of a business that sells drone video services. All the pages will need to be in the similar design style.
The video's are targeted at consumers that want to sell there home and would like to have a cool drone video of photos of their home.

How does the website look:
- has a navbar on top
- A cool looking banner of an areal drone.
- A Big header: with company name: SkyLoftReels
- A smaller subheader: We film your home to increase your chances of sale
- Then a section with a Big header: How does it work
- In this section a place for a vimeo explainitory video
- Then a similar navbar styled bar with a phone number and a email address
- Then a section where the videos porfolio is displayed in a cool way
- Inside this sectiona header: Our work

- A section with header: Why us?
- 4 symbols here with a subheader and some lorum ipsum text underneath (see wireframe images)

- Under that a: Contact us
- where you can put in name, email, phone, message box and a send button

- At the bottom a footer with phone number and a fake address for now.

Be creative. Use creative but serious color.
Use a serious font. Make it a sharp design. Sharp lines. Not to dark design and not to light design.

The wireframes are the same kind of images.
PLEASE PUT IN DESIGNS OF ALL THE PAGES

Good luck

Target Market(s)

People that want to sell home and want to make a cool drone video or photos of their home.

Industry/Entity Type

Business

Contact Information for Business Card

Lucas Wenning
lucas@skyloftreels.example
+31647208351

Logo Text

SkyLoftReels

Number of Pages Required

1 page

Font styles to use
Sans Serif

Requirements
Must have
• All the sections as explained in the instructions.
• The nav bar should have an about us, services, portfolio and a contact us buttons.
• See instruction for details.
• Must include designs of the front page, contact us, our services, portfolio and contact us.
• If you do add some designs for the "about us", "services", "prices", "portfolio" and "contact us" pages, you make a way better chance of winning the competition.
Nice to have
• designs for the other pages as described at the Must haves. You make a better chance of winning if you include them. Look at the wireframes to see the mockups for those pages. think creative about what kind of sections and design should be included in those pages.
Should not have
• bad designs.

```html
<!DOCTYPE html>
<html lang="en">
<head>
<meta charset="utf-8">
<title>SkyLoftReels – Home</title>
<link rel="stylesheet" href="https://fonts.googleapis.com/css2?family=Kanit:wght@400;500&family=Open+Sans:wght@400;600&family=Lato:wght@400;700&display=swap">
<style>
  :root {
    --orange: #f15a29;
    --orange-dark: #c8431a;
    --ink: #1d1d1d;
    --text: #333333;
    --muted: #9a9a9a;
    --rule: #cfcfcf;
    --bg-light: #f2f2f2;
    --bg-soft: #efefef;
    --bg-contact: #f7f7f7;
    --footer: #333333;
    --white: #ffffff;
  }
  * { box-sizing: border-box; margin: 0; padding: 0; }
  html, body { width: 1200px; height: 2338px; overflow: hidden; }
  body { font-family: "Open Sans", sans-serif; color: var(--text); background: var(--white); position: relative; }

  /* Header */
  .site-header { height: 101px; border-top: 4px solid var(--orange); position: relative; background: var(--white); }
  .brand { position: absolute; left: 81px; top: 28px; display: flex; align-items: center; gap: 12px; }
  .brand-dot { width: 30px; height: 30px; border-radius: 50%; background: var(--ink); }
  .brand-name { font-family: "Kanit", sans-serif; font-weight: 500; font-size: 32px; color: var(--orange); }
  .header-phone { position: absolute; right: 81px; top: 16px; display: flex; align-items: center; gap: 8px; font-size: 19px; color: var(--ink); }
  .main-nav { position: absolute; right: 73px; top: 64px; display: flex; }
  .main-nav a { font-size: 14px; color: var(--ink); text-decoration: none; padding: 0 28px; border-left: 1px solid var(--rule); line-height: 20px; position: relative; }
  .main-nav a:first-child { border-left: none; }
  .main-nav a.active { color: var(--orange); }
  .main-nav a.active::after { content: ""; position: absolute; left: 28px; right: 28px; bottom: -7px; height: 3px; background: var(--orange); }

  /* Hero */
  .hero { height: 480px; position: relative; background: linear-gradient(100deg, #5d6b3c 0%, #a9b59a 22%, #a9c4e0 45%, #8fb2d8 75%, #c9d8e8 100%); }
  .hero-arrow { position: absolute; top: 316px; width: 24px; height: 28px; background: rgba(255,255,255,.55); display: flex; align-items: center; justify-content: center; }
  .hero-arrow.prev { left: 0; } .hero-arrow.next { right: 0; }
  .hero-caption { position: absolute; left: 0; right: 0; bottom: 0; height: 98px; background: rgba(20,20,20,.82); text-align: center; color: var(--white); font-family: "Kanit", sans-serif; font-weight: 500; }
  .hero-title { font-size: 31px; line-height: 38px; padding-top: 12px; letter-spacing: .5px; }
  .hero-sub { font-size: 29px; line-height: 36px; }

  /* Section headings */
  .section-title { font-family: "Open Sans", sans-serif; font-size: 30px; font-weight: 400; text-align: center; color: var(--ink); text-transform: uppercase; }
  .section-title .accent { color: var(--orange); }
  .divider { position: relative; width: 488px; height: 14px; margin: 0 auto; }
  .divider::before { content: ""; position: absolute; left: 0; right: 0; top: 6px; height: 1px; background: var(--rule); }
  .divider .dots { position: absolute; left: 50%; top: 0; transform: translateX(-50%); display: flex; gap: 4px; background: inherit; padding: 0 4px; }
  .divider .dots i { width: 12px; height: 12px; border-radius: 50%; background: #c4c4c4; display: block; }
  .divider .dots i:nth-child(2) { width: 14px; height: 14px; margin-top: -1px; }

  /* How it works */
  .how { height: 513px; background: var(--bg-light); padding-top: 38px; position: relative; }
  .how .divider { margin-top: 18px; }
  .video-frame { position: absolute; left: 277px; top: 143px; width: 642px; height: 370px; background: linear-gradient(180deg, #2b2b2b 0%, #5f7f9e 40%, #c9b28a 75%, #e8c4a8 100%); display: flex; align-items: center; justify-content: center; }
  .play { width: 84px; height: 84px; border-radius: 50%; background: var(--orange); border: 4px solid var(--white); display: flex; align-items: center; justify-content: center; }

  /* Contact strip */
  .contact-strip { height: 43px; background: var(--orange); display: flex; justify-content: center; align-items: center; gap: 44px; font-family: "Kanit", sans-serif; font-weight: 500; font-size: 21px; color: var(--white); }
  .strip-item { display: flex; align-items: center; gap: 12px; }
  .strip-icon { width: 34px; height: 43px; background: var(--orange-dark); display: flex; align-items: center; justify-content: center; }

  /* Our work */
  .work { height: 395px; background: var(--white); padding-top: 30px; position: relative; }
  .work .divider { margin-top: 20px; }
  .work-grid { position: absolute; left: 81px; top: 131px; display: flex; gap: 3px; }
  .work-item { width: 344px; height: 220px; position: relative; display: flex; align-items: center; justify-content: center; }
  .work-item:nth-child(1) { background: linear-gradient(180deg, #c8d3dc 0%, #7d8e7a 60%, #5b6a4f 100%); }
  .work-item:nth-child(2) { background: linear-gradient(180deg, #7fb6e6 0%, #b5a08a 55%, #5f7a45 100%); }
  .work-item:nth-child(3) { background: linear-gradient(90deg, #4f7a3a 0%, #c9c6bd 40%, #d9d6cf 100%); }
  .work-item .play { width: 52px; height: 52px; border-width: 3px; background: rgba(255,255,255,.9); }
  .work-caption { position: absolute; left: 0; right: 0; bottom: 0; height: 34px; background: rgba(25,25,25,.72); color: var(--white); font-family: "Lato", sans-serif; font-weight: 700; font-size: 13px; display: flex; align-items: center; justify-content: center; }
  .work-arrow { position: absolute; top: 230px; }
  .work-arrow.prev { left: 38px; } .work-arrow.next { right: 38px; }

  /* Why us */
  .why { height: 380px; background: var(--bg-soft); padding-top: 30px; position: relative; }
  .why .divider { margin-top: 20px; }
  .why .divider .dots, .how .divider .dots { background: transparent; }
  .features { position: absolute; left: 43px; top: 160px; display: flex; }
  .feature { width: 266px; text-align: center; position: relative; }
  .feature + .feature::before { content: ""; position: absolute; left: 0; top: 36px; height: 142px; width: 1px; background: #dcdcdc; }
  .feature-icon { height: 90px; display: flex; align-items: flex-end; justify-content: center; }
  .feature-title { font-family: "Kanit", sans-serif; font-weight: 500; font-size: 23px; color: var(--ink); margin-top: 8px; }
  .feature.highlight .feature-title { color: var(--orange); }
  .feature-text { font-family: "Lato", sans-serif; font-size: 15px; line-height: 20px; color: var(--ink); margin-top: 6px; }
  .feature-text .more { font-weight: 700; }
  .feature.highlight .more { color: var(--orange); }

  /* Contact */
  .contact { height: 381px; background: var(--bg-contact); padding-top: 28px; position: relative; }
  .contact .divider { margin-top: 18px; }
  .contact-intro { font-family: "Lato", sans-serif; font-size: 16px; text-align: center; color: var(--ink); margin-top: 30px; }
  .contact-form { position: absolute; left: 349px; top: 169px; width: 499px; }
  .form-grid { display: grid; grid-template-columns: 238px 238px; column-gap: 23px; }
  .form-col { display: flex; flex-direction: column; gap: 9px; }
  .field { height: 25px; border: 1px solid #d6d6d6; background: var(--white); font-family: "Lato", sans-serif; font-style: italic; font-size: 11px; color: var(--muted); padding: 5px 9px; }
  .field.message { height: 61px; }
  .submit { margin-top: 14px; width: 499px; height: 50px; background: var(--orange); border: none; border-radius: 2px; color: var(--white); font-family: "Kanit", sans-serif; font-weight: 500; font-size: 22px; }

  /* Footer */
  .site-footer { height: 45px; background: var(--footer); color: #e6e6e6; font-family: "Lato", sans-serif; font-size: 14px; display: flex; align-items: center; justify-content: center; }
</style>
</head>
<body>
  <header class="site-header">
    <div class="brand"><span class="brand-dot"></span><span class="brand-name">SkyLoftReels</span></div>
    <div class="header-phone">
      <svg width="24" height="24" viewBox="0 0 24 24"><circle cx="12" cy="12" r="11" fill="none" stroke="#f15a29" stroke-width="1.6"/><path d="M8 6l2 3-1.3 1.4c.8 1.8 2 3 3.9 3.9L14 13l3 2-1 2.2c-4.8-.3-9-4.5-9.2-9.2z" fill="#f15a29"/></svg>
      <span>123 456 7890</span>
    </div>
    <nav class="main-nav">
      <a href="#" class="active">HOME</a>
      <a href="#">ABOUT US</a>
      <a href="#">SERVCIES</a>
      <a href="#">PORTFOLIO</a>
      <a href="#">CONTACT US</a>
    </nav>
  </header>

  <section class="hero" role="img" aria-label="Banner photo of a hexacopter drone with camera flying against a blue sky">
    <span class="hero-arrow prev"><svg width="8" height="12" viewBox="0 0 8 12"><path d="M6 1L1 6l5 5" fill="none" stroke="#666" stroke-width="1.5"/></svg></span>
    <span class="hero-arrow next"><svg width="8" height="12" viewBox="0 0 8 12"><path d="M2 1l5 5-5 5" fill="none" stroke="#666" stroke-width="1.5"/></svg></span>
    <div class="hero-caption">
      <h1 class="hero-title">SKYLOFTREELS</h1>
      <p class="hero-sub">We Film Your Home To Increase Your Chances of Sale</p>
    </div>
  </section>

  <section class="how">
    <h2 class="section-title"><span class="accent">How does</span> it work?</h2>
    <div class="divider"><span class="dots"><i></i><i></i><i></i></span></div>
    <div class="video-frame" role="img" aria-label="Explainer video: hands holding a tablet showing a drone pilot filming a house">
      <span class="play"><svg width="34" height="38" viewBox="0 0 34 38"><path d="M4 2l28 17L4 36z" fill="#fff"/></svg></span>
    </div>
  </section>

  <div class="contact-strip">
    <div class="strip-item">
      <span class="strip-icon"><svg width="22" height="22" viewBox="0 0 24 24"><circle cx="12" cy="12" r="10.5" fill="none" stroke="#fff" stroke-width="1.6"/><path d="M8 6l2 3-1.3 1.4c.8 1.8 2 3 3.9 3.9L14 13l3 2-1 2.2c-4.8-.3-9-4.5-9.2-9.2z" fill="#fff"/></svg></span>
      <span>Call Us - 31 647208351</span>
    </div>
    <div class="strip-item">
      <span class="strip-icon"><svg width="22" height="16" viewBox="0 0 22 16"><rect x="1" y="1" width="20" height="14" fill="#fff"/><path d="M1 1l10 8 10-8" fill="none" stroke="#c8431a" stroke-width="1.6"/></svg></span>
      <span>Mail Us - contact@skyloftreels.example</span>
    </div>
  </div>

  <section class="work">
    <h2 class="section-title"><span class="accent">Our</span> work</h2>
    <div class="divider"><span class="dots"><i></i><i></i><i></i></span></div>
    <svg class="work-arrow prev" width="16" height="26" viewBox="0 0 16 26"><path d="M14 2L3 13l11 11" fill="none" stroke="#bbb" stroke-width="3"/></svg>
    <div class="work-grid">
      <div class="work-item" role="img" aria-label="Portfolio video: drone hovering over green hills"><span class="play"><svg width="20" height="22" viewBox="0 0 20 22"><path d="M3 1l16 10L3 21z" fill="#1d1d1d"/></svg></span><span class="work-caption">Loren Ipsum Dolor Sit</span></div>
      <div class="work-item" role="img" aria-label="Portfolio video: drone above a row of brick houses"><span class="play"><svg width="20" height="22" viewBox="0 0 20 22"><path d="M3 1l16 10L3 21z" fill="#1d1d1d"/></svg></span><span class="work-caption">Loren Ipsum Dolor Sit</span></div>
      <div class="work-item" role="img" aria-label="Portfolio video: drone in front of a house entrance"><span class="play"><svg width="20" height="22" viewBox="0 0 20 22"><path d="M3 1l16 10L3 21z" fill="#1d1d1d"/></svg></span><span class="work-caption">Loren Ipsum Dolor Sit</span></div>
    </div>
    <svg class="work-arrow next" width="16" height="26" viewBox="0 0 16 26"><path d="M2 2l11 11L2 24" fill="none" stroke="#bbb" stroke-width="3"/></svg>
  </section>

  <section class="why">
    <h2 class="section-title"><span class="accent">Why</span> us?</h2>
    <div class="divider"><span class="dots"><i></i><i></i><i></i></span></div>
    <div class="features">
      <div class="feature highlight">
        <div class="feature-icon"><svg width="88" height="90" viewBox="0 0 88 90"><circle cx="50" cy="16" r="14" fill="#f15a29"/><text x="50" y="23" text-anchor="middle" font-family="Kanit, sans-serif" font-size="20" fill="#fff">$</text><ellipse cx="44" cy="60" rx="36" ry="24" fill="#f15a29"/><rect x="20" y="72" width="10" height="16" fill="#f15a29"/><rect x="56" y="72" width="10" height="16" fill="#f15a29"/><rect x="74" y="54" width="12" height="10" rx="3" fill="#f15a29"/><rect x="38" y="40" width="16" height="3" fill="#fff"/></svg></div>
        <h3 class="feature-title">Cheap</h3>
        <p class="feature-text">Lorem ipsum dolor sit amet,<br>consectetuer adipis <span class="more">...[+]</span></p>
      </div>
      <div class="feature">
        <div class="feature-icon"><svg width="84" height="84" viewBox="0 0 84 84"><path d="M42 10a32 32 0 0 0-28 47l10-6a20 20 0 0 1 18-29v10l16-16L42 0z" fill="#1d1d1d"/><path d="M42 74a32 32 0 0 0 28-47l-10 6a20 20 0 0 1-18 29V52L26 68l16 16z" fill="#1d1d1d"/></svg></div>
        <h3 class="feature-title">Flexible</h3>
        <p class="feature-text">Lorem ipsum dolor sit amet,<br>consectetuer adipis <span class="more">...[+]</span></p>
      </div>
      <div class="feature">
        <div class="feature-icon"><svg width="86" height="86" viewBox="0 0 86 86"><polygon points="43,2 53,13 68,9 71,24 84,32 76,45 84,58 70,64 67,79 52,75 43,86 33,75 18,79 15,64 2,58 10,45 2,32 15,24 18,9 33,13" fill="#1d1d1d"/><path d="M30 42h7v18h-7zM40 42l6-12c3 0 4 2 3 6l-1 5h9c2 0 3 2 2 4l-4 13c-1 2-2 2-4 2H40z" fill="#fff"/></svg></div>
        <h3 class="feature-title">Quality</h3>
        <p class="feature-text">Lorem ipsum dolor sit amet,<br>consectetuer adipis <span class="more">...[+]</span></p>
      </div>
      <div class="feature">
        <div class="feature-icon"><svg width="88" height="90" viewBox="0 0 88 90"><text x="30" y="22" text-anchor="middle" font-family="Kanit, sans-serif" font-size="24" fill="#1d1d1d">$</text><rect x="38" y="50" width="9" height="16" fill="#1d1d1d"/><rect x="50" y="40" width="9" height="26" fill="#1d1d1d"/><rect x="62" y="30" width="9" height="36" fill="#1d1d1d"/><path d="M36 44L70 10" stroke="#1d1d1d" stroke-width="5"/><path d="M60 6h16v16z" fill="#1d1d1d"/><path d="M4 70l16-10h22l-4 8H26l40 0 14-10 4 4-18 20H4z" fill="#1d1d1d"/></svg></div>
        <h3 class="feature-title">Increase Sale Chance</h3>
        <p class="feature-text">Lorem ipsum dolor sit amet,<br>consectetuer adipis <span class="more">...[+]</span></p>
      </div>
    </div>
  </section>

  <section class="contact">
    <h2 class="section-title"><span class="accent">Contact</span> us</h2>
    <div class="divider"><span class="dots"><i></i><i></i><i></i></span></div>
    <p class="contact-intro">Fill In The Form Below And We Will Get Back To You Within 48 Hours.</p>
    <form class="contact-form">
      <div class="form-grid">
        <div class="form-col">
          <div class="field">First Name</div>
          <div class="field">Last Name</div>
          <div class="field">Phone Number</div>
        </div>
        <div class="form-col">
          <div class="field">Email</div>
          <div class="field message">Message</div>
        </div>
      </div>
      <button type="button" class="submit">SUBMIT</button>
    </form>
  </section>

  <footer class="site-footer">Copyright © 2016 SkyLoftReels .&nbsp; All Right Reserved.</footer>
</body>
</html>
```